Calder Vossik - Cinematographer

NEED:
I'm looking for a sleek, professional, modern business card that will give give the recipient the impression that they can trust their production will go smoothly by hiring me. I will bring creativity and knowledge to their shoot, so that we can create powerful images.
I am looking for a card with a strong style and design ethos that could be expanded to a website and a full visual/graphic/design entity for me.
ABOUT ME:
I am a mid-twenties cinematographer, I work on music video, narrative short, commercial, and corporate projects. I blend the science and artistry of cameras and filmmaking to tell a story. I'm an artist, a technician, and a manager.
DESIGN:
I like sleek, simple design. Black, dark grays, white, dark navy, steel blues, I love cyan, but also cyan and red. I am not a fan of earthy tones. I generally prefer modern, san-serif fonts over serifs. My old logo was based on an aperture, a multi-blade device at the back of a lens that controls how much light passes through, but I made it with so many colors, that it doesn't necessarily lend itself to a specific color-scheme or design ethos. I liked that the aperture design provided a sense of the technical requirements of my job. I'm a fan of matte business cards, but am open to plenty of specialty print processes to make an outstanding card.
ATTACHED FILES:
My Old Rainbox Aperture Logo, plus a few designs I've tried playing around with, but am not tied to. I AM OPEN TO NEW DESIGNS, DO NOT FEEL TIED TO THIS.
**I've pulled my old logo down from the attached files, and instead attached other business cards I like, so as not to mislead you where I would like to go.
INFO:
Name: Calder Vossik
Job: Cinematographer
Email: ccvossik@lumenpost.net
Phone: 415.555.0193
Website: caldervossik.com
Updates
I'm adding some images of other cards that I like, and removing my old logo, since I'm looking for something new, and don't want that old logo to push anyone a certain direction.

```html
<!DOCTYPE html>
<html lang="en">
<head>
<meta charset="utf-8">
<title>Calder Vossik – Cinematographer Business Card</title>
<link href="https://fonts.googleapis.com/css2?family=Oswald:wght@200;300&display=swap" rel="stylesheet">
<style>
  :root {
    --backdrop: #dcefed;
    --card: #231f20;
    --lens-fill: #332f30;
    --guide: #e4f4f2;
    --cyan: #7dd3c8;
    --white: #f4f7f7;
  }
  * { box-sizing: border-box; margin: 0; padding: 0; }
  html, body {
    width: 900px;
    height: 1200px;
    overflow: hidden;
    background: var(--backdrop);
    font-family: "Oswald", "Arial Narrow", sans-serif;
  }
  .canvas { position: relative; width: 900px; height: 1200px; }
  .card {
    position: absolute;
    left: 137px;
    width: 626px;
    height: 387px;
    background: var(--card);
    overflow: hidden;
  }
  .card--front { top: 181px; }
  .card--back { top: 632px; }
  .card__guides { position: absolute; inset: 0; width: 626px; height: 387px; }

  .front-mark {
    position: absolute;
    left: 236px;
    top: 128px;
    display: flex;
    align-items: center;
    gap: 14px;
    font-weight: 200;
    font-size: 52px;
    line-height: 1;
    letter-spacing: 1px;
    text-transform: uppercase;
    color: var(--cyan);
    white-space: nowrap;
  }
  .front-mark__square {
    display: block;
    width: 22px;
    height: 22px;
    background: var(--cyan);
  }

  .back-mark {
    position: absolute;
    left: 49px;
    top: 33px;
    width: 122px;
    text-align: center;
    font-weight: 300;
    font-size: 22px;
    line-height: 1.05;
    text-transform: uppercase;
    color: var(--cyan);
  }

  .identity {
    position: absolute;
    left: 304px;
    top: 24px;
    color: var(--white);
    text-transform: uppercase;
    white-space: nowrap;
  }
  .identity__name { font-weight: 200; font-size: 40px; line-height: 1; }
  .identity__surname { font-size: 30px; }
  .identity__role {
    margin-top: 28px;
    font-weight: 200;
    font-size: 40px;
    line-height: 1;
    color: var(--cyan);
  }

  .contact {
    position: absolute;
    right: 28px;
    bottom: 30px;
    list-style: none;
    text-align: right;
    color: var(--white);
    font-weight: 200;
    font-size: 21px;
    line-height: 31px;
    text-transform: uppercase;
    white-space: nowrap;
  }
</style>
</head>
<body>
<main class="canvas">

  <section class="card card--front" aria-label="Card front">
    <svg class="card__guides" viewBox="0 0 626 387" aria-hidden="true">
      <circle cx="118" cy="280" r="176" fill="var(--lens-fill)"/>
      <circle cx="109" cy="266" r="204" fill="none" stroke="var(--guide)" stroke-width="2"/>
      <line x1="109" y1="0" x2="109" y2="387" stroke="var(--guide)" stroke-width="2"/>
      <line x1="0" y1="266" x2="626" y2="266" stroke="var(--guide)" stroke-width="2"/>
    </svg>
    <p class="front-mark">Calder Vossik<span class="front-mark__square"></span></p>
  </section>

  <section class="card card--back" aria-label="Card back">
    <svg class="card__guides" viewBox="0 0 626 387" aria-hidden="true">
      <circle cx="109" cy="86" r="100" fill="var(--lens-fill)" stroke="var(--guide)" stroke-width="2"/>
      <circle cx="109" cy="86" r="126" fill="none" stroke="var(--guide)" stroke-width="2"/>
      <line x1="109" y1="0" x2="109" y2="387" stroke="var(--guide)" stroke-width="2"/>
      <line x1="0" y1="86" x2="623" y2="86" stroke="var(--guide)" stroke-width="2"/>
    </svg>
    <p class="back-mark">Calder<br>Vossik</p>

    <header class="identity">
      <h1 class="identity__name">Calder <span class="identity__surname">Vossik</span></h1>
      <p class="identity__role">Cinematographer</p>
    </header>

    <ul class="contact">
      <li>415.555.0193</li>
      <li>caldervossik.com</li>
      <li>ccvossik@lumenpost.net</li>
    </ul>
  </section>

</main>
</body>
</html>
```